Working Capital graphics

Our business advisory firm requires 9 images to be re-created and improved in the branding of our business.

The 9 images have been uploaded below and the colours and branding of the business can be found at the website www.tallowmereadvisory.com.au

```html
<!DOCTYPE html>
<html lang="en">
<head>
<meta charset="utf-8">
<title>Working Capital Cycle</title>
<link rel="stylesheet" href="https://fonts.googleapis.com/css2?family=Jost:wght@600&display=swap">
<style>
  :root {
    --frame-grey: #d6d9dd;
    --paper: #ffffff;
    --brand-navy: #1b2a47;
    --brand-teal: #1f6e78;
    --brand-aqua: #3fa9b5;
    --brand-gold: #c99a3b;
    --label: #ffffff;
  }
  html, body {
    margin: 0;
    padding: 0;
    width: 1036px;
    height: 1200px;
    overflow: hidden;
    background: var(--paper);
  }
  .canvas {
    display: block;
    width: 1036px;
    height: 1200px;
  }
  .frame { fill: var(--paper); stroke: var(--frame-grey); stroke-width: 14; }
  .gear-receivable { fill: var(--brand-navy); }
  .gear-inventory { fill: var(--brand-teal); }
  .gear-payable { fill: var(--brand-aqua); }
  .cycle-arc { fill: none; stroke: var(--brand-gold); stroke-width: 14; }
  .cycle-head { fill: var(--brand-gold); }
  .gear-label {
    font-family: "Jost", "Futura", sans-serif;
    font-weight: 600;
    fill: var(--label);
    text-anchor: middle;
    letter-spacing: 1px;
  }
</style>
</head>
<body>
<svg class="canvas" viewBox="0 0 1574 1824" xmlns="http://www.w3.org/2000/svg" role="img" aria-label="Working capital cycle: accounts receivable, inventory and accounts payable">
  <defs>
    <g id="gear-teeth">
      <circle r="196"/>
      <rect x="-51" y="-240" width="102" height="480"/>
      <rect x="-51" y="-240" width="102" height="480" transform="rotate(45)"/>
      <rect x="-51" y="-240" width="102" height="480" transform="rotate(90)"/>
      <rect x="-51" y="-240" width="102" height="480" transform="rotate(135)"/>
    </g>
  </defs>

  <rect class="frame" x="7" y="7" width="1560" height="1810"/>

  <g class="cycle-arrow">
    <path class="cycle-arc" d="M720,272 A350 350 0 0 1 1262,458"/>
    <polygon class="cycle-head" points="1220,464 1300,448 1276,527"/>
  </g>
  <g class="cycle-arrow">
    <path class="cycle-arc" d="M280,786 A362 362 0 0 0 470,1330"/>
    <polygon class="cycle-head" points="473,1286 537,1341 458,1366"/>
  </g>
  <g class="cycle-arrow">
    <path class="cycle-arc" d="M1345,1138 A356 356 0 0 1 980,1578"/>
    <polygon class="cycle-head" points="986,1538 910,1568 975,1618"/>
  </g>

  <g class="gear gear-receivable" transform="translate(920,565) rotate(18)">
    <use href="#gear-teeth"/>
  </g>
  <g class="gear gear-inventory" transform="translate(582,965)">
    <use href="#gear-teeth"/>
  </g>
  <g class="gear gear-payable" transform="translate(1024,1221)">
    <use href="#gear-teeth"/>
  </g>

  <text class="gear-label" font-size="60" x="920" y="568">ACCOUNTS</text>
  <text class="gear-label" font-size="60" x="920" y="627">RECEIVABLE</text>
  <text class="gear-label" font-size="66" x="582" y="992">INVENTORY</text>
  <text class="gear-label" font-size="60" x="1024" y="1230">ACCOUNTS</text>
  <text class="gear-label" font-size="60" x="1024" y="1290">PAYABLE</text>
</svg>
</body>
</html>
```